Marlowe Group needs a business card

I would like the card to be simple but modern and elegant.
I like black and white.
or black and gold.
we are a private finance lender and also are involved in property and property developments.

please look at the business card photos i provided i would like M.G only one one side and all the other details on the other side use fonts that tie in with my theme.

Industry/Entity Type

Finance

Contact Information for Business Card

Marlowe Group (M.G) Daniel Marlowe M: 0413586207 E: danmarl@inboxmail.test

Font styles to use
Other font styles liked:
• Use fonts that would reflect our business

Colors
000000
ffffff

Requirements
Must have
• one side of details
• other side has either M.G or Marlowe Group like in the photos provided

```html
<!DOCTYPE html>
<html lang="en">
<head>
<meta charset="utf-8">
<title>Marlowe Group — Business Card</title>
<link rel="stylesheet" href="https://fonts.googleapis.com/css2?family=Cinzel:wght@400;700&family=Open+Sans:wght@400;600&display=swap">
<style>
  :root {
    --backdrop-top: #7a7a7a;
    --backdrop-bottom: #9a9a9a;
    --card-black: #000000;
    --gold: #f2c21b;
    --gold-light: #ffe27a;
    --gold-deep: #e0a81a;
    --sun: #ffcc33;
    --sun-light: #ffe07a;
    --white: #ffffff;
  }
  * { margin: 0; padding: 0; box-sizing: border-box; }
  html, body { width: 1200px; height: 900px; overflow: hidden; }
  body {
    position: relative;
    background: linear-gradient(180deg, var(--backdrop-top), var(--backdrop-bottom));
    font-family: "Open Sans", Arial, sans-serif;
  }
  .card {
    position: absolute;
    top: 170px;
    width: 347px;
    height: 561px;
    overflow: hidden;
  }
  .card-front { left: 259px; background: var(--card-black); }
  .card-back {
    left: 631px;
    background: linear-gradient(160deg, var(--sun) 0%, #ffd34a 45%, var(--sun) 100%);
  }
  .gold-tab {
    position: absolute;
    left: 101px;
    width: 144px;
    height: 29px;
    background: linear-gradient(180deg, var(--gold-light), var(--gold));
  }
  .gold-tab.top { top: 0; height: 30px; }
  .gold-tab.bottom { bottom: 0; height: 28px; }
  .brand-mark {
    position: absolute;
    top: 100px;
    left: 0;
    width: 100%;
    text-align: center;
    font-family: "Cinzel", Georgia, serif;
    font-weight: 400;
    font-size: 104px;
    line-height: 1;
    color: var(--gold);
  }
  .company-name {
    position: absolute;
    top: 266px;
    left: 0;
    width: 100%;
    text-align: center;
    font-family: "Cinzel", Georgia, serif;
    font-weight: 400;
    font-size: 25px;
    letter-spacing: 0.5px;
    color: var(--gold);
  }
  .person-name {
    position: absolute;
    top: 372px;
    left: 0;
    width: 100%;
    text-align: center;
    font-family: "Cinzel", Georgia, serif;
    font-weight: 700;
    font-size: 25px;
    color: var(--gold);
  }
  .contact {
    position: absolute;
    top: 438px;
    left: 0;
    width: 100%;
    text-align: center;
    color: var(--white);
    font-size: 18px;
    line-height: 24px;
  }
  .contact .label { color: var(--gold); font-weight: 600; }
  .glow-band {
    position: absolute;
    background: rgba(255, 255, 255, 0.18);
    border-radius: 14px;
  }
  .streak {
    position: absolute;
    height: 20px;
    background: linear-gradient(90deg, rgba(255,255,255,0), rgba(255,255,255,0.55), rgba(255,255,255,0.2));
  }
  .back-mark {
    position: absolute;
    top: 196px;
    left: 0;
    width: 100%;
    text-align: center;
    font-family: "Cinzel", Georgia, serif;
    font-weight: 400;
    font-size: 120px;
    line-height: 1;
    color: var(--white);
  }
</style>
</head>
<body>
  <section class="card card-front" aria-label="Card front with contact details">
    <div class="gold-tab top"></div>
    <div class="brand-mark">M.G</div>
    <p class="company-name">Marlowe Group</p>
    <p class="person-name">Daniel Marlowe</p>
    <p class="contact">
      <span class="label">M:</span> 0413586207<br>
      <span class="label">E:</span> danmarl@inboxmail.test
    </p>
    <div class="gold-tab bottom"></div>
  </section>

  <section class="card card-back" aria-label="Card back with monogram">
    <div class="streak" style="top:38px; left:100px; width:247px;"></div>
    <div class="glow-band" style="top:155px; left:-20px; width:170px; height:260px;"></div>
    <div class="glow-band" style="top:155px; left:190px; width:180px; height:260px;"></div>
    <div class="glow-band" style="top:258px; left:-20px; width:400px; height:180px; background:rgba(255,255,255,0.1);"></div>
    <div class="streak" style="top:505px; left:280px; width:67px;"></div>
    <div class="back-mark">M.G</div>
  </section>
</body>
</html>
```